Wren Hollow Farm Postcard Design

I am looking for a new postcard design to mail out this season. We are a Farm business that does wholesale and retail and bulk seasoned firewood sales. we sell firewood from anything from bagged wood to tractor trailer loads of wood. We sell firewood in bulk bags. Pick up or delivery available there is no order to big or too small. I need my business name and phone number on the cards Wren Hollow Farm 615-302-4187 (call or text) I would like it to say we are the best priced guaranteed. I want something that is simple and straight forward but also really catches the eye when they see these in the mail box. I attached my logo and feel free to use photos of split firewood if you would like. id like my email on the card Wrenhollowfarm47@maplepost.net.

Target Market(s)

Firewood purchasers

Industry/Entity Type

agriculture

Requirements
Must have
• email phone number logo

```html
<!DOCTYPE html>
<html lang="en">
<head>
<meta charset="utf-8">
<title>Wren Hollow Farm Postcard</title>
<link href="https://fonts.googleapis.com/css2?family=Lobster+Two:ital,wght@1,700&family=Open+Sans:wght@400;700;800&display=swap" rel="stylesheet">
<style>
  :root {
    --orange: #d97a35;
    --orange-light: #f0a666;
    --white: #ffffff;
    --ink: #0d0d0d;
    --wood-dark: #3d2a1c;
    --wood-mid: #8a5a34;
    --wood-light: #d9a774;
    --grass: #4f7a34;
  }
  * { margin: 0; padding: 0; box-sizing: border-box; }
  html, body { width: 850px; height: 1200px; overflow: hidden; background: var(--white); }
  .postcard {
    position: relative; width: 850px; height: 1200px; overflow: hidden;
    font-family: "Open Sans", Arial, sans-serif; background: var(--white);
  }
  .hero-photo {
    position: absolute; left: 0; top: 0; width: 850px; height: 795px;
    background:
      radial-gradient(ellipse at 12% 45%, rgba(79,122,52,.85) 0%, rgba(79,122,52,0) 30%),
      radial-gradient(ellipse at 70% 60%, var(--wood-light) 0%, rgba(217,167,116,0) 45%),
      linear-gradient(135deg, var(--wood-dark) 0%, var(--wood-mid) 45%, #b5804f 65%, var(--wood-dark) 100%);
  }
  .footer-photo {
    position: absolute; left: 0; top: 1132px; width: 850px; height: 68px;
    background: linear-gradient(90deg, var(--wood-dark), var(--wood-mid) 50%, var(--wood-dark));
  }
  .band { position: absolute; left: 0; width: 850px; background: var(--orange); }
  .band--top { top: 787px; height: 18px; }
  .band--bottom { top: 1108px; height: 22px; }

  .brand {
    position: absolute; left: 0; top: 30px; width: 430px; height: 112px;
    background: var(--white); border-bottom: 4px solid var(--orange);
    display: flex; align-items: center; padding-left: 25px;
  }
  .brand__name { font-weight: 800; font-size: 33px; line-height: 1; color: var(--ink); }

  .headline {
    position: absolute; left: 0; width: 850px; text-align: center;
    font-family: "Lobster Two", "Brush Script MT", cursive; font-style: italic; font-weight: 700;
    color: var(--white); font-size: 56px; line-height: 1;
    text-shadow: 0 2px 6px rgba(0,0,0,.5);
  }
  .headline--one { top: 162px; }
  .headline--two { top: 228px; }
  .headline-box {
    position: absolute; left: 88px; top: 290px; width: 672px; height: 112px;
    background: var(--white); transform: rotate(1.6deg);
  }
  .headline-box__text {
    position: absolute; left: 0; top: 290px; width: 850px; text-align: center;
    font-family: "Lobster Two", "Brush Script MT", cursive; font-style: italic; font-weight: 700;
    font-size: 100px; line-height: 108px; color: var(--orange);
    text-shadow: 0 3px 3px rgba(0,0,0,.35);
  }

  .photo-circle {
    position: absolute; top: 416px; width: 214px; height: 214px; border-radius: 50%;
    border: 4px solid var(--white); box-shadow: 0 4px 10px rgba(0,0,0,.4);
  }
  .photo-circle--bag { left: 190px; background: radial-gradient(circle at 40% 60%, #e8e4dc 0%, #b89a74 40%, #5e7d3e 80%); }
  .photo-circle--splitter { left: 440px; background: radial-gradient(circle at 50% 60%, #c98a4e 0%, #e8a326 40%, #1f3a2a 80%); }

  .steps { position: absolute; left: 0; top: 690px; width: 850px; height: 220px; }

  .contact-phone {
    position: absolute; left: 172px; top: 920px; height: 80px; display: flex; align-items: center;
  }
  .contact-phone__number { font-weight: 800; font-size: 72px; color: var(--ink); letter-spacing: -1px; margin-left: 18px; line-height: 1; }
  .contact-email {
    position: absolute; left: 78px; top: 1004px; height: 54px; display: flex; align-items: center;
  }
  .contact-email__address { font-weight: 700; font-size: 31px; color: var(--ink); margin-left: 18px; line-height: 1; }
</style>
</head>
<body>
<main class="postcard">
  <div class="hero-photo" role="img" aria-label="Photo of a large stack of cut hardwood logs with grass at the left"></div>
  <div class="band band--top"></div>

  <header class="brand">
    <div class="brand__name">WREN HOLLOW FARM</div>
  </header>

  <h1>
    <span class="headline headline--one">Ignite Cozy Nights</span>
    <span class="headline headline--two">Without Burning</span>
    <span class="headline-box"></span>
    <span class="headline-box__text">Your Budget!</span>
  </h1>

  <div class="photo-circle photo-circle--bag" role="img" aria-label="Photo of a mesh bag of split firewood in front of stacked logs"></div>
  <div class="photo-circle photo-circle--splitter" role="img" aria-label="Photo of a worker operating a yellow and green firewood processor"></div>

  <svg class="steps" width="850" height="220" viewBox="0 0 850 220" aria-label="Click, order, glow">
    <defs>
      <radialGradient id="burst" cx="50%" cy="45%" r="55%">
        <stop offset="0" stop-color="#f0a666"/>
        <stop offset="1" stop-color="#d97a35"/>
      </radialGradient>
      <g id="starburst">
        <rect x="-72" y="-72" width="144" height="144" fill="url(#burst)"/>
        <rect x="-72" y="-72" width="144" height="144" fill="url(#burst)" transform="rotate(15)"/>
        <rect x="-72" y="-72" width="144" height="144" fill="url(#burst)" transform="rotate(30)"/>
        <rect x="-72" y="-72" width="144" height="144" fill="url(#burst)" transform="rotate(45)"/>
        <rect x="-72" y="-72" width="144" height="144" fill="url(#burst)" transform="rotate(60)"/>
        <rect x="-72" y="-72" width="144" height="144" fill="url(#burst)" transform="rotate(75)"/>
      </g>
    </defs>
    <g font-family="Open Sans, Arial, sans-serif" font-weight="800" font-size="46" fill="#fff" text-anchor="middle">
      <g transform="translate(200 103)"><use href="#starburst"/><text y="-2">CLICK</text>
        <g stroke="#fff" stroke-width="4" stroke-linecap="round" fill="none">
          <path d="M-20 30 l-8 -8 M-12 22 l0 -10 M-28 38 l-12 0"/>
        </g>
        <path d="M-10 30 L20 54 L6 56 L14 70 L8 73 L0 58 L-10 66 Z" fill="#fff"/>
      </g>
      <g transform="translate(423 103)"><use href="#starburst"/><text y="-2">ORDER</text>
        <g stroke="#fff" stroke-width="4" fill="none" stroke-linecap="round" stroke-linejoin="round">
          <path d="M-30 22 h8 l8 34 h30 l6 -24 h-40"/>
          <path d="M-4 42 l6 6 l10 -10"/>
        </g>
        <circle cx="-10" cy="66" r="4" fill="#fff"/><circle cx="14" cy="66" r="4" fill="#fff"/>
      </g>
      <g transform="translate(647 103)"><use href="#starburst"/><text y="-2">GLOW</text>
        <path d="M0 18 C12 32 22 44 20 58 C18 70 8 76 0 76 C-12 76 -22 68 -22 56 C-22 46 -14 40 -12 30 C-6 38 -4 44 -2 48 C4 40 4 30 0 18 Z" fill="#fff"/>
      </g>
      <g fill="none" stroke="#0d0d0d" stroke-width="3">
        <path d="M282 172 Q305 190 334 170"/>
        <path d="M498 172 Q521 190 550 170"/>
      </g>
      <path d="M334 170 l-10 -2 l6 10 Z M550 170 l-10 -2 l6 10 Z" fill="#0d0d0d"/>
    </g>
  </svg>

  <div class="contact-phone">
    <svg width="56" height="56" viewBox="0 0 56 56" aria-hidden="true">
      <circle cx="28" cy="28" r="26" fill="var(--orange)"/>
      <path d="M18 16 c2 -2 5 -2 6 0 l3 6 c1 2 0 3 -2 4 c1 4 4 7 8 8 c1 -2 2 -3 4 -2 l6 3 c2 1 2 4 0 6 c-3 3 -7 3 -11 1 c-7 -4 -12 -9 -15 -16 c-2 -4 -2 -8 1 -10 Z" fill="#fff"/>
    </svg>
    <span class="contact-phone__number">615-302-4187</span>
  </div>

  <div class="contact-email">
    <svg width="52" height="52" viewBox="0 0 52 52" aria-hidden="true">
      <circle cx="26" cy="26" r="25" fill="var(--orange)"/>
      <g fill="none" stroke="#fff" stroke-width="2.5">
        <circle cx="26" cy="26" r="15"/>
        <ellipse cx="26" cy="26" rx="7" ry="15"/>
        <path d="M11 26 h30 M14 18 h24 M14 34 h24"/>
      </g>
    </svg>
    <span class="contact-email__address">WRENHOLLOWFARM47@MAPLEPOST.NET</span>
  </div>

  <div class="band band--bottom"></div>
  <div class="footer-photo" role="img" aria-label="Strip photo of stacked logs on the ground"></div>
</main>
</body>
</html>
```